Heron Loan Partners Business Card

We need a business card design for our mortgage servicing company. In addition to servicing the loans of homeowners, we help homeowners with purchasing their homes and any mortgage refinancing. We would like to see designs that use the colors in the logo attached below (gold-ish yellow and navy blue), and any other design you deem fit! The design should communicate a simpler life with smart mortgages provided by Heron.

```html
<!DOCTYPE html>
<html lang="en">
<head>
<meta charset="utf-8">
<title>Heron Loan Partners – Business Card</title>
<link rel="stylesheet" href="https://fonts.googleapis.com/css2?family=Montserrat:wght@400;600&display=swap">
<style>
  :root {
    --backdrop: #549bb5;
    --gold: #dfb23f;
    --navy: #27235e;
    --paper: #ffffff;
  }
  * { margin: 0; padding: 0; box-sizing: border-box; }
  html, body { width: 1008px; height: 1200px; overflow: hidden; }
  body { background: var(--backdrop); font-family: "Montserrat", sans-serif; position: relative; }

  .card {
    position: absolute;
    left: 112px;
    width: 778px;
    height: 444px;
    background: var(--paper);
    overflow: hidden;
  }
  .card--front { top: 114px; }
  .card--back { top: 623px; }

  .front__panel {
    position: absolute;
    left: 0; top: 0;
    width: 385px; height: 100%;
    background: var(--gold);
    color: var(--paper);
  }
  .holder {
    position: absolute;
    right: 29px; top: 58px;
    text-align: right;
  }
  .holder__name { font-size: 24px; font-weight: 400; letter-spacing: 0.2px; line-height: 1.1; }
  .holder__name strong { font-weight: 600; }
  .holder__role { font-size: 17px; font-weight: 400; line-height: 1.3; }

  .contact {
    position: absolute;
    right: 29px; top: 340px;
    list-style: none;
    text-align: right;
  }
  .contact__item {
    display: flex; align-items: center; justify-content: flex-end; gap: 3px;
    font-size: 24px; line-height: 31px; letter-spacing: 0.3px;
  }
  .contact__icon { width: 18px; height: 18px; flex: none; }

  .brand {
    position: absolute;
    display: flex; align-items: center; gap: 10px;
    color: var(--navy);
    font-weight: 600;
    white-space: nowrap;
  }
  .brand__dot { border-radius: 50%; background: var(--gold); flex: none; }
  .brand--front { left: 430px; top: 205px; font-size: 27px; }
  .brand--front .brand__dot { width: 20px; height: 20px; }
  .brand--back { left: 50%; top: 185px; transform: translateX(-50%); font-size: 42px; }
  .brand--back .brand__dot { width: 30px; height: 30px; }

  .website {
    position: absolute;
    left: 0; right: 0; top: 375px;
    text-align: center;
    color: var(--gold);
    font-size: 22px;
    letter-spacing: 11px;
  }
</style>
</head>
<body>
  <section class="card card--front" aria-label="Business card front">
    <div class="front__panel">
      <div class="holder">
        <p class="holder__name"><strong>DANIEL</strong>ASHFORD</p>
        <p class="holder__role">OWNER</p>
      </div>
      <ul class="contact">
        <li class="contact__item">heron@heronloans.com
          <svg class="contact__icon" viewBox="0 0 18 18" aria-hidden="true">
            <circle cx="9" cy="9" r="9" fill="#fff"/>
            <rect x="4.5" y="5.8" width="9" height="6.4" rx="1" fill="none" stroke="#dfb23f" stroke-width="1.4"/>
            <path d="M4.8 6.2 9 9.4l4.2-3.2" fill="none" stroke="#dfb23f" stroke-width="1.4"/>
          </svg>
        </li>
        <li class="contact__item">555-014-2290
          <svg class="contact__icon" viewBox="0 0 18 18" aria-hidden="true">
            <circle cx="9" cy="9" r="9" fill="#fff"/>
            <path d="M6 4.8c-1.2 1-1.2 3 .6 5.2 1.8 2.2 3.8 3.2 5.2 2.4l.8-.8-1.8-1.8-1.1.7c-.8-.4-1.8-1.5-2.1-2.3l.7-1.1-1.8-1.8z" fill="#dfb23f"/>
          </svg>
        </li>
      </ul>
    </div>
    <div class="brand brand--front"><span class="brand__dot"></span>Heron Loan Partners</div>
  </section>

  <section class="card card--back" aria-label="Business card back">
    <div class="brand brand--back"><span class="brand__dot"></span>Heron Loan Partners</div>
    <p class="website">www.heronloanpartners.com</p>
  </section>
</body>
</html>
```